International business needs business cards

Our company, DRV Ventures Inc. is in the business of supplying a range construction products with particular emphasis on CEMENT. We have developed our own brand - TORVAN SUPPLIES - with which to infiltrate the market. We are launching our brand of cement (TORVAN Type IS Cement) into the Caribbean which is unlike anything this market has ever seen. A monopoly has existed here for the past 60-odd years and the market has now opened to allow the importation of other brands and consumers are anxious and ready for change/improvement. We are very excited to be launching and want to make a great first impression. We will be conducting workshops and seminars (from government level to the hardware store owners) and we want our business card to give us the strong, confident introduction that we need.

Target Market(s)

construction; builders; engineers; home owners

Industry/Entity Type

Construction

Contact Information for Business Card

Marisol Depree
CEO
cell # 1 555 4180736
Ground floor,Lindell Plaza Suite 2734
George Town,Grand Cayman
Cayman Islands,KY1-4823
EMAIL: m.depree@drvventuresinc.example
web site drvventuresinc.example

COMPANY: skype info drv.ventures.example

second card
Yvette Brannock-Depree
CFO
CELL# 1 555 607 3941
George Town,Grand Cayman
Cayman Islands,KY1-4823
EMAIL: y.brannockdepree@drvventuresinc.example
website drvventuresinc.example

Requirements
Must have
• Business cards must display BOTH logos - DRV is the company and TORVAN is the brand.

```html
<!DOCTYPE html>
<html lang="en">
<head>
<meta charset="utf-8">
<title>DRV Ventures Inc. — Business Card</title>
<link rel="stylesheet" href="https://fonts.googleapis.com/css2?family=PT+Sans:wght@400;700&display=swap">
<style>
  :root {
    --page-bg: #e8e3de;
    --panel-red: #7c1c27;
    --panel-red-deep: #4a0b12;
    --panel-text: #f3dfe2;
    --panel-text-soft: #e2c2c7;
    --rule: rgba(243, 223, 226, 0.75);
    --divider: #2a0a0e;
    --frost-light: #f4f3f1;
    --frost-mid: #dcdad6;
    --ink: #1b1b1b;
    --mark-red: #6e1420;
  }
  * { box-sizing: border-box; margin: 0; padding: 0; }
  html, body {
    width: 1200px; height: 969px; overflow: hidden;
    background: var(--page-bg);
    font-family: "PT Sans", sans-serif;
  }
  .business-card {
    position: absolute; left: 100px; top: 201px;
    width: 1000px; height: 567px;
    display: flex;
    box-shadow: 0 10px 30px rgba(0,0,0,0.18);
  }
  .contact-panel {
    position: relative;
    width: 498px; height: 100%;
    background: linear-gradient(100deg, var(--panel-red) 0%, #6a1520 60%, var(--panel-red-deep) 100%);
    color: var(--panel-text);
  }
  .panel-divider { width: 5px; height: 100%; background: var(--divider); }
  .brand-panel {
    position: relative; flex: 1; height: 100%;
    background: radial-gradient(ellipse at 60% 40%, var(--frost-light) 0%, var(--frost-mid) 100%);
  }
  .person-name { position: absolute; left: 57px; top: 62px; font-size: 32px; font-weight: 700; }
  .person-title { position: absolute; left: 57px; top: 104px; font-size: 25px; color: var(--panel-text-soft); }
  .dotted-rule {
    position: absolute; left: 57px; width: 390px;
    border-top: 2px dotted var(--rule);
  }
  .rule-top { top: 168px; }
  .rule-bottom { top: 371px; }
  .address { position: absolute; left: 57px; top: 200px; font-size: 25px; line-height: 36px; font-style: normal; color: var(--panel-text-soft); }
  .contact-list { position: absolute; left: 57px; top: 408px; list-style: none; font-size: 25px; color: var(--panel-text-soft); }
  .contact-list li { display: flex; align-items: center; height: 40px; }
  .contact-list svg { width: 22px; height: 22px; margin-right: 17px; flex: none; fill: var(--panel-text-soft); }
  .company-mark {
    position: absolute; left: 86px; top: 118px;
    display: flex; align-items: center; gap: 16px;
  }
  .company-square { width: 110px; height: 110px; background: var(--mark-red); }
  .company-name { font-size: 40px; font-weight: 700; color: var(--ink); line-height: 1.05; }
  .brand-mark {
    position: absolute; left: 239px; top: 270px; width: 0;
    display: flex; flex-direction: column; align-items: center;
  }
  .brand-circle { width: 140px; height: 140px; border-radius: 50%; background: var(--ink); flex: none; }
  .brand-name { margin-top: 16px; font-size: 30px; font-weight: 700; color: var(--ink); letter-spacing: 4px; white-space: nowrap; }
</style>
</head>
<body>
  <section class="business-card" aria-label="DRV Ventures Inc. business card">
    <div class="contact-panel">
      <h1 class="person-name">Marisol Depree</h1>
      <p class="person-title">CEO</p>
      <div class="dotted-rule rule-top"></div>
      <address class="address">
        Ground floor<br>
        Lindell Plaza Suite 2734<br>
        George Town,Grand Cayman<br>
        Cayman Islands,KY1-4823
      </address>
      <div class="dotted-rule rule-bottom"></div>
      <ul class="contact-list">
        <li>
          <svg viewBox="0 0 24 24" aria-hidden="true"><path d="M7 1h10a2 2 0 0 1 2 2v18a2 2 0 0 1-2 2H7a2 2 0 0 1-2-2V3a2 2 0 0 1 2-2zm0 3v14h10V4H7zm5 15.5a1.2 1.2 0 1 0 0 2.4 1.2 1.2 0 0 0 0-2.4z"/></svg>
          1 555 4180736
        </li>
        <li>
          <svg viewBox="0 0 24 24" aria-hidden="true"><path d="M2 5h20v14H2V5zm2 2v.6l8 5.2 8-5.2V7H4zm16 3l-8 5.2L4 10v7h16v-7z"/></svg>
          m.depree@drvventuresinc.example
        </li>
        <li>
          <svg viewBox="0 0 24 24" aria-hidden="true"><path d="M12 2a10 10 0 1 0 0 20 10 10 0 0 0 0-20zm-1 17.9A8 8 0 0 1 4.1 11H7c.1 3.2 1.5 6.4 4 8.9zM4.1 9A8 8 0 0 1 11 4.1C8.6 6.6 7.2 8 7 9H4.1zM13 4.1A8 8 0 0 1 19.9 9H17c-.2-1-1.6-2.4-4-4.9zM9 11h6c-.1 2.6-1.1 5.2-3 7.3-1.9-2.1-2.9-4.7-3-7.3zm0-2c.3-1.2 1.3-2.6 3-4.3 1.7 1.7 2.7 3.1 3 4.3H9zm4 10.9c2.5-2.5 3.9-5.7 4-8.9h2.9a8 8 0 0 1-6.9 8.9z"/></svg>
          www.drvventuresinc.example
        </li>
      </ul>
    </div>
    <div class="panel-divider"></div>
    <div class="brand-panel">
      <div class="company-mark">
        <span class="company-square" aria-hidden="true"></span>
        <span class="company-name">DRV<br>Ventures Inc.</span>
      </div>
      <div class="brand-mark">
        <span class="brand-circle" aria-hidden="true"></span>
        <span class="brand-name">TORVAN</span>
      </div>
    </div>
  </section>
</body>
</html>
```